Machining Business Order Thank You Insert

I am looking for a business style card to include with orders that I ship. The card needs to thank the recipient for their order, and encourage them to leave a review. The card should include my business name and contact information and have an area to hand write a message.

I mainly sale on Craftlane and my own website. We are a machining an manufacturing business that are in the sale of mostly metal machined and 3d printed plastic products.

The front of the card should include the following:
Logo: (attached)
Snapgram: https://www.snapgram.example/kelvomill/
Friendsbook: https://www.friendsbook.example/KelvoMill
Website: https://www.kelvomill.example/

The back of the card needs an area to write a message

Industry/Entity Type

3D Printing, Machining, Craftlane

Contact Information for Business Card

Black or white front, white back to write a personal message

Font styles to use
Sans Serif

Colors

Designer to choose colors to be used in the design.

Requirements
Must have
• Encourage a review, social media info

```html
<!DOCTYPE html>
<html lang="en">
<head>
<meta charset="utf-8">
<title>KelvoMill – Order Thank You Insert</title>
<link rel="stylesheet" href="https://fonts.googleapis.com/css2?family=Barlow:wght@400;500;600&family=Kaushan+Script&display=swap">
<style>
  :root {
    --stage: #8c8f90;
    --card-white: #ffffff;
    --card-dark-a: #1b1c1c;
    --card-dark-b: #2f3130;
    --orange: #e4572a;
    --orange-faint: #fde3d8;
    --grey-mark: #6b6c6d;
    --grey-text: #8e8f90;
    --grey-url: #4a4b4c;
  }
  * { box-sizing: border-box; margin: 0; padding: 0; }
  html, body {
    width: 1200px; height: 928px; overflow: hidden;
    background: var(--stage);
    font-family: "Barlow", Arial, sans-serif;
  }
  .card {
    position: absolute; left: 264px; width: 672px; height: 384px;
    border-radius: 16px; overflow: hidden;
  }
  .card--message { top: 58px; background: var(--card-white); }
  .card--thanks {
    top: 484px;
    background: linear-gradient(180deg, var(--card-dark-b) 0%, var(--card-dark-a) 60%, var(--card-dark-a) 100%);
  }

  /* message side */
  .watermark-name {
    position: absolute; left: 0; right: 0; top: 120px;
    text-align: center; font-size: 84px; font-weight: 600;
    letter-spacing: 10px; color: var(--orange-faint);
  }
  .site-link {
    position: absolute; left: 0; right: 0; top: 328px;
    display: flex; justify-content: center; align-items: center; gap: 8px;
    font-size: 18px; font-weight: 500; letter-spacing: 1px; color: var(--grey-url);
  }
  .site-link svg { width: 20px; height: 20px; }

  /* thank-you side */
  .brand {
    position: absolute; left: 60px; top: 150px; width: 230px;
    display: flex; align-items: center; gap: 12px;
  }
  .brand-square { width: 22px; height: 22px; background: var(--orange); flex: none; }
  .brand-name {
    font-size: 30px; font-weight: 500; letter-spacing: 6px; color: var(--orange);
  }
  .thanks {
    position: absolute; left: 330px; width: 300px; top: 100px; text-align: center;
  }
  .thanks-title {
    font-family: "Kaushan Script", cursive; font-size: 58px; line-height: 1;
    white-space: nowrap;
  }
  .thanks-title .word-thank { color: var(--orange); }
  .thanks-title .word-you { color: var(--grey-mark); }
  .thanks-sub {
    margin-top: 12px; font-size: 26px; font-weight: 500; letter-spacing: 2px;
    color: var(--grey-text);
  }
  .thanks-sub .accent { color: var(--orange); font-weight: 600; }
  .review-call {
    margin-top: 16px; font-size: 21px; font-weight: 600; letter-spacing: 1.5px;
    color: var(--orange);
  }
  .socials {
    margin-top: 12px; display: flex; justify-content: center; gap: 16px;
    font-size: 18px; letter-spacing: 1px; color: var(--grey-text); white-space: nowrap;
  }
  .socials span { display: flex; align-items: center; gap: 6px; }
  .socials i { display: block; width: 18px; height: 18px; border-radius: 3px; background: var(--orange); }
</style>
</head>
<body>
  <section class="card card--message">
    <div class="watermark-name" aria-hidden="true">KELVOMILL</div>
    <p class="site-link">
      <svg viewBox="0 0 20 20" aria-hidden="true">
        <circle cx="10" cy="10" r="9" fill="var(--orange)"/>
        <ellipse cx="10" cy="10" rx="4" ry="9" fill="none" stroke="#fff" stroke-width="1.3"/>
        <line x1="1" y1="10" x2="19" y2="10" stroke="#fff" stroke-width="1.3"/>
      </svg>
      www.kelvomill.example
    </p>
  </section>

  <section class="card card--thanks">
    <div class="brand">
      <span class="brand-square"></span>
      <span class="brand-name">KELVOMILL</span>
    </div>
    <div class="thanks">
      <h1 class="thanks-title"><span class="word-thank">Thank</span> <span class="word-you">You</span></h1>
      <p class="thanks-sub">FOR YOUR <span class="accent">ORDER</span></p>
      <p class="review-call">Leave A Review:</p>
      <p class="socials">
        <span><i></i>@kelvomill</span>
        <span><i></i>@KelvoMill</span>
      </p>
    </div>
  </section>
</body>
</html>
```